Visitenkarten-Design für Sonnen-/Fensterschutz
Zielgruppe
KLW GmbH ist eine Firma, die Sonnenschutz und Fensterschutz anbieten.
'Ihr kompetenter Partner in Sachen Sonnenschutz- , Fenster- und Türtechnik. Sie erhalten echtes Handwerk aus dem Mühlviertel zu fairen Preisen.'
Unsere Zielgruppe sind Personen mit Haus, die am Land leben.
Firmenname: KLW GmbH
Slogan: Fenster & Sonnenschutz
Aufgabenstellung
Hier befindet sich das Logodesign: https://dx.qv/t-QwLpo7RbNs
Bitte ein schlichtes Design bereitstellen mit einer Dummy-Person:
Jonas Weidlinger + Telefonnummer + Email
Die finalen Daten bitte erst am Schluss berücksichtigen (für Gewinnerdesign)
Gerne auch hintern + vorne bedruckbar bereitstellen.

```html
<!DOCTYPE html>
<html lang="de">
<head>
<meta charset="utf-8">
<title>KLW GmbH – Visitenkarte</title>
<link href="https://fonts.googleapis.com/css2?family=Open+Sans:wght@400;600&family=Poppins:wght@400;600;700&display=swap" rel="stylesheet">
<style>
  :root {
    --stage: #575757;
    --paper: #ffffff;
    --orange: #ee6a1f;
    --red: #e03a22;
    --deep-red: #a81e1e;
    --text-grey: #555555;
    --line-grey: #d6d6d6;
  }
  * { box-sizing: border-box; margin: 0; padding: 0; }
  html, body {
    width: 1200px; height: 1200px; overflow: hidden;
    background: var(--stage);
  }
  .stage { position: relative; width: 1200px; height: 1200px; }

  .card {
    position: absolute; left: 259px; width: 667px; height: 431px;
    background: var(--paper); overflow: hidden;
  }
  .card--front { top: 102px; }
  .card--back { top: 613px; left: 258px; }

  /* shared brand */
  .brand {
    position: absolute; font-family: "Poppins", sans-serif; font-weight: 700;
    color: var(--orange); letter-spacing: 1px; line-height: 1;
    white-space: nowrap; display: flex; align-items: center;
  }
  .brand-mark { display: inline-block; flex: none; background: var(--orange); }
  .slogan {
    position: absolute; font-family: "Poppins", sans-serif; font-weight: 600;
    color: var(--deep-red); text-transform: uppercase; white-space: nowrap;
    border-top: 2px solid var(--red); text-align: right; line-height: 1.2;
  }

  /* front */
  .front-bands { position: absolute; left: 0; top: 172px; width: 215px; height: 90px; }
  .front-brand { left: 250px; top: 176px; font-size: 58px; gap: 16px; }
  .front-brand .brand-mark { width: 48px; height: 48px; }
  .front-slogan { left: 322px; top: 250px; width: 300px; font-size: 19px; padding-top: 3px; }

  /* back */
  .divider { position: absolute; left: 299px; top: 39px; width: 1px; height: 324px; background: var(--line-grey); }
  .person { position: absolute; left: 22px; width: 300px; top: 168px; text-align: center; font-family: "Open Sans", sans-serif; color: var(--text-grey); }
  .person-name { font-size: 24px; font-weight: 400; }
  .person-role { font-size: 18px; font-weight: 600; margin-top: 4px; }

  .back-brand { left: 334px; top: 44px; font-size: 40px; gap: 10px; }
  .back-brand .brand-mark { width: 28px; height: 28px; }
  .back-slogan { left: 432px; top: 96px; width: 176px; font-size: 12px; border-top-width: 1.5px; padding-top: 2px; }

  .contact { position: absolute; left: 385px; top: 198px; font-family: "Poppins", sans-serif; color: var(--text-grey); }
  .contact-company { font-size: 15px; font-weight: 600; }
  .contact-row { display: flex; align-items: flex-start; gap: 6px; font-size: 19px; line-height: 21px; margin-top: 8px; }
  .contact-row svg { flex: none; width: 22px; height: 22px; }
  .contact-row--phone { margin-top: 12px; }

  .back-bands { position: absolute; left: 0; top: 362px; width: 667px; height: 52px; }
</style>
</head>
<body>
<main class="stage">
  <section class="card card--front" aria-label="Vorderseite">
    <svg class="front-bands" viewBox="0 0 215 90" preserveAspectRatio="none" aria-hidden="true">
      <defs>
        <linearGradient id="bandFront" x1="0" y1="0" x2="1" y2="0">
          <stop offset="0" stop-color="#e03a22"/><stop offset="1" stop-color="#ee6a1f"/>
        </linearGradient>
      </defs>
      <rect x="0" y="0" width="173" height="6" fill="url(#bandFront)"/>
      <rect x="0" y="28" width="185" height="21" fill="url(#bandFront)"/>
      <rect x="0" y="65" width="210" height="25" fill="url(#bandFront)"/>
    </svg>
    <div class="brand front-brand"><span class="brand-mark"></span>KLW GmbH</div>
    <div class="slogan front-slogan">Fenster &amp; Sonnenschutz</div>
  </section>

  <section class="card card--back" aria-label="Rückseite">
    <div class="person">
      <p class="person-name">Jonas Weidlinger</p>
      <p class="person-role">Geschäftsführer</p>
    </div>
    <div class="divider"></div>

    <div class="brand back-brand"><span class="brand-mark"></span>KLW GmbH</div>
    <div class="slogan back-slogan">Fenster &amp; Sonnenschutz</div>

    <div class="contact">
      <p class="contact-company">KLW GmbH</p>
      <div class="contact-row">
        <svg viewBox="0 0 22 22" aria-hidden="true"><path d="M2 3 L20 11 L2 19 L6 11 Z" fill="#e03a22"/></svg>
        <p>Am Lindenhang 7-9<br>30519 Hannover</p>
      </div>
      <div class="contact-row contact-row--phone">
        <svg viewBox="0 0 22 22" aria-hidden="true"><path d="M5 2 L9 6 L7 9 C8 12 10 14 13 15 L16 13 L20 17 L17 20 C9 19 3 13 2 5 Z" fill="#e03a22"/></svg>
        <p>+49 151 204 8836</p>
      </div>
      <div class="contact-row">
        <svg viewBox="0 0 22 22" aria-hidden="true"><rect x="2" y="5" width="18" height="13" fill="#e03a22"/><path d="M2 5 L11 12 L20 5" fill="none" stroke="#fff" stroke-width="1.6"/></svg>
        <p>+49 151 204 8836</p>
      </div>
    </div>

    <svg class="back-bands" viewBox="0 0 667 52" preserveAspectRatio="none" aria-hidden="true">
      <defs>
        <linearGradient id="bandBack" x1="0" y1="0" x2="1" y2="0">
          <stop offset="0" stop-color="#e03a22"/><stop offset="1" stop-color="#ee6a1f"/>
        </linearGradient>
      </defs>
      <rect x="0" y="4" width="667" height="3" fill="url(#bandBack)"/>
      <rect x="0" y="16" width="667" height="9" fill="url(#bandBack)"/>
      <rect x="0" y="32" width="667" height="14" fill="url(#bandBack)"/>
    </svg>
  </section>
</main>
</body>
</html>
```